Bright Harbor Web Design & Marketing

Will award a 2nd place prize of $100.00 if someone can come up with a logo to match this design!
Updates

Okay, I'm really looking to see some better designs here. What do you think will bring the best designs out? Please remember with all future submissions I'm looking for a cartoon style / illustrator style website. I'm not sure what the technical term is for it, so I uploaded some images in the brief.

Target Market(s)

Small Business Owners

Industry/Entity Type

Marketing

Logo Text

BrightHarbor.com

Number of Pages Required

1 page

Colors

Designer to choose colors to be used in the design.

Requirements
Must have
• Logo should say BrightHarbor.com I would like more than just a text logo. I want some sort of cool custom graphic / icon with it that will look nice on shirts/hats/etc

```html
<!DOCTYPE html>
<html lang="en">
<head>
<meta charset="utf-8">
<title>Bright Harbor Web Design &amp; Marketing</title>
<link href="https://fonts.googleapis.com/css2?family=Cinzel:wght@400;700&family=Open+Sans:wght@400;600;700&family=Tinos:wght@400;700&display=swap" rel="stylesheet">
<style>
:root{
  --orange:#f47b20;
  --orange-dark:#d9650f;
  --ink:#1f2329;
  --text:#555a60;
  --muted:#8a8f96;
  --white:#ffffff;
  --hero-a:#6a5ec9;
  --hero-b:#4f86e3;
  --night:#1a1d2b;
  --cream:#f6f4ef;
  --sky:#dce8f5;
  --slate:#4a4f57;
  --blue:#1f6fc4;
  --footer:#1d222c;
}
*{box-sizing:border-box;margin:0;padding:0}
html,body{width:1200px;height:4737px;overflow:hidden}
body{position:relative;background:var(--white);font-family:"Tinos",serif;color:var(--text)}
section,header,footer{position:absolute;left:0;width:1200px;overflow:hidden}
.abs{position:absolute}
.section-title{position:absolute;left:0;width:1200px;text-align:center;font-family:"Cinzel",serif;font-size:28px;letter-spacing:2px;color:var(--ink)}
.section-lead{position:absolute;left:150px;width:900px;text-align:center;font-size:13px;line-height:19px;color:var(--text)}
.placeholder{position:absolute}

/* header */
.site-header{top:0;height:594px;background:linear-gradient(135deg,var(--hero-a),var(--hero-b))}
.nav-bar{position:absolute;top:0;left:0;width:1200px;height:95px}
.brand{position:absolute;left:140px;top:28px;display:flex;align-items:center;gap:10px}
.brand-dot{width:34px;height:34px;border-radius:50%;background:var(--orange)}
.brand-name{font-family:"Open Sans",sans-serif;font-weight:700;font-size:24px;color:var(--white)}
.menu{position:absolute;top:0;left:537px;display:flex;height:95px}
.menu-item{display:flex;flex-direction:column;align-items:center;justify-content:center;padding:0 14px;height:95px;font-family:"Open Sans",sans-serif;font-size:12px;font-weight:600;color:var(--white);text-transform:uppercase;gap:8px}
.menu-item.active{background:var(--orange)}
.menu-item svg{width:26px;height:26px}
.hero-art{left:560px;top:110px;width:520px;height:484px;border-radius:14px 14px 0 0;background:radial-gradient(circle at 55% 40%,#f3c46a 0%,#e2a24a 30%,#8e5fc9 60%,rgba(90,110,220,0) 80%)}
.hero-title{position:absolute;left:145px;top:100px;width:520px;font-family:"Open Sans",sans-serif;font-weight:700;font-size:39px;line-height:50px;color:var(--white)}
.hero-title em{font-style:normal;color:#ffe07a}
.hero-call{position:absolute;left:145px;top:525px;display:flex;align-items:center;gap:14px;font-family:"Open Sans",sans-serif;font-weight:700;font-size:26px;color:var(--white)}
.hero-call .call-icon{width:50px;height:50px;border-radius:50%;background:rgba(255,255,255,.2);display:flex;align-items:center;justify-content:center}
.slide-arrow{position:absolute;top:350px;width:26px;height:30px;background:rgba(0,0,0,.55);display:flex;align-items:center;justify-content:center}

/* about */
.about{top:594px;height:322px;background:var(--white)}
.about .section-title span{color:var(--orange)}
.btn{display:inline-flex;align-items:center;gap:8px;height:40px;padding:0 18px;font-family:"Open Sans",sans-serif;font-size:14px;color:var(--white);border-radius:3px}
.btn-orange{background:var(--orange)}
.btn-slate{background:var(--slate)}
.about-actions{position:absolute;top:225px;left:0;width:1200px;display:flex;justify-content:center;gap:16px}

/* services */
.services{top:916px;height:758px;background:linear-gradient(180deg,#252a3a 0%,var(--night) 55%,#2a2233 100%)}
.services .section-title,.services .section-lead{color:var(--white)}
.service-label{position:absolute;width:210px;font-family:"Open Sans",sans-serif}
.service-label h4{font-size:12px;font-weight:700;color:#ffd23f;margin-bottom:4px}
.service-label p{font-size:11px;line-height:14px;color:#d6d8de}
.service-label.left{text-align:right}

/* plans */
.plans{top:1674px;height:657px;background:#f4f4f4}
.floor{position:absolute;left:0;top:505px;width:1200px;height:152px;background:linear-gradient(180deg,#c98a52,#9d6535)}
.plan-card{position:absolute;top:142px;width:198px;height:440px;background:var(--white);border-top:4px solid var(--orange);box-shadow:0 4px 14px rgba(0,0,0,.15);text-align:center;font-family:"Open Sans",sans-serif}
.plan-card.featured{top:126px;height:456px}
.plan-icon{margin:26px auto 14px;width:56px;height:56px;border-radius:50%;background:#eef3f8;display:flex;align-items:center;justify-content:center}
.plan-name{font-size:16px;font-weight:600;color:var(--ink)}
.plan-from{margin-top:14px;font-size:10px;color:var(--muted)}
.plan-price{font-size:40px;color:var(--ink);font-weight:400;line-height:48px}
.plan-price sup{font-size:16px}
.plan-price small{font-size:14px}
.plan-features{list-style:none;text-align:left;margin:18px 18px 0;font-family:"Tinos",serif;font-size:12px;color:var(--text)}
.plan-features li{padding:6px 0 6px 14px;border-bottom:1px solid #eee;position:relative}
.plan-features li::before{content:"›";position:absolute;left:2px;top:4px;color:var(--orange)}
.plan-foot{position:absolute;bottom:22px;left:0;width:100%;display:flex;flex-direction:column;align-items:center;gap:8px}
.plan-btn{width:120px;height:30px;line-height:30px;font-size:12px;color:var(--white);background:var(--slate)}
.plan-btn.primary{background:var(--orange)}
.plan-more{font-size:11px;color:var(--text)}

/* video */
.video{top:2331px;height:606px}
.video-scene{left:0;top:0;width:1200px;height:606px;background:linear-gradient(180deg,#dfe6ec 0%,#b9c3cc 45%,#7c8590 75%,#5a616a 100%)}
.video-screen{left:370px;top:120px;width:460px;height:290px;background:linear-gradient(135deg,#4b5fa8,#6a82d2);border:10px solid #1b1c20;border-radius:8px}
.play{position:absolute;left:569px;top:233px;width:62px;height:62px;border-radius:50%;background:var(--white);display:flex;align-items:center;justify-content:center}
.video .section-title{top:56px}
.video-band{position:absolute;left:0;top:506px;width:1200px;height:100px;background:rgba(20,22,28,.88);display:flex;align-items:center;justify-content:center;text-align:center}
.video-band p{width:920px;font-family:"Cinzel",serif;font-size:17px;line-height:26px;letter-spacing:1px;color:var(--white)}

/* clients */
.clients{top:2937px;height:253px;background:var(--cream)}
.client-row{position:absolute;top:190px;left:150px;width:900px;display:flex;justify-content:space-between;align-items:center}
.client{display:flex;align-items:center;gap:6px;font-family:"Open Sans",sans-serif;font-weight:600;font-size:15px;color:#333}
.client i{width:12px;height:12px;background:#333;display:block;border-radius:50%}
.row-arrow{position:absolute;top:192px;font-family:"Open Sans",sans-serif;font-size:24px;color:#999}

/* why */
.why{top:3190px;height:521px;background:var(--sky)}
.why-item{position:absolute;width:270px;font-family:"Open Sans",sans-serif}
.why-item h4{font-size:13px;font-weight:700;color:var(--orange);margin-bottom:4px}
.why-item p{font-family:"Tinos",serif;font-size:12px;line-height:16px;color:var(--text)}
.why-item.right h4{color:var(--blue)}
.why-icon{position:absolute;width:44px;height:44px;border-radius:6px;display:flex;align-items:center;justify-content:center}

/* team */
.team{top:3711px;height:363px;background:var(--white)}
.team-card{position:absolute;top:180px;width:420px;height:140px;border:1px solid #e4e4e4;background:var(--white);font-family:"Open Sans",sans-serif}
.team-photo{position:absolute;left:18px;top:-16px;width:78px;height:84px;background:linear-gradient(160deg,#9fb0c2,#5c6e82)}
.team-name{position:absolute;left:112px;top:16px;font-size:14px;font-weight:700;color:var(--ink)}
.team-role{position:absolute;left:112px;top:36px;font-size:12px;color:var(--orange)}
.team-bio{position:absolute;left:18px;top:80px;width:384px;font-family:"Tinos",serif;font-size:12px;line-height:16px;color:var(--text)}

/* inquiry */
.inquiry{top:4074px;height:379px;background:var(--white)}
.inquiry-art{left:0;top:80px;width:440px;height:299px;background:linear-gradient(120deg,#e9edf1 0%,#c8d0d8 55%,#aab4bf 100%)}
.field{position:absolute;font-family:"Open Sans",sans-serif;font-size:11px;color:var(--text)}
.field span{display:block;margin-bottom:6px}
.field div{height:28px;border-bottom:1px solid #cfd3d8}
.field.area div{height:76px;border:1px solid #cfd3d8}
.submit{position:absolute;left:488px;top:318px;width:90px;height:32px;background:var(--blue);color:var(--white);font-family:"Open Sans",sans-serif;font-size:12px;font-weight:700;display:flex;align-items:center;justify-content:center}

/* footer */
.site-footer{top:4453px;height:284px;background:linear-gradient(180deg,#2b3240,var(--footer) 60%,#151922)}
.foot-col{position:absolute;top:36px;font-family:"Open Sans",sans-serif;font-size:12px;color:#d0d4da}
.foot-col h5{font-family:"Cinzel",serif;font-size:14px;font-weight:700;color:var(--white);margin-bottom:16px;letter-spacing:1px}
.foot-col h5 span{color:var(--orange)}
.foot-col li{list-style:none;line-height:20px}
.foot-col li::before{content:"› ";color:var(--orange)}
.contact-line{display:flex;align-items:center;gap:8px;line-height:22px}
.contact-line b{width:16px;height:16px;border-radius:50%;background:var(--orange);display:block}
.news-input{margin-top:12px;width:210px;height:26px;background:var(--white);color:#888;font-size:11px;padding:5px 8px}
.news-btn{margin-top:10px;width:100px;height:28px;background:var(--blue);color:var(--white);font-weight:700;display:flex;align-items:center;justify-content:center}
.copyright{position:absolute;left:0;bottom:0;width:1200px;height:31px;background:#0f1217;display:flex;justify-content:space-between;align-items:center;padding:0 145px;font-family:"Open Sans",sans-serif;font-size:11px;color:var(--orange)}
</style>
</head>
<body>

<header class="site-header">
  <div class="nav-bar">
    <div class="brand"><span class="brand-dot"></span><span class="brand-name">BrightHarbor.com</span></div>
    <nav class="menu">
      <div class="menu-item active"><svg viewBox="0 0 24 24" fill="#fff"><path d="M12 3 2 12h3v8h5v-5h4v5h5v-8h3z"/></svg>Home</div>
      <div class="menu-item"><svg viewBox="0 0 24 24" fill="#fff"><circle cx="12" cy="12" r="4"/><path d="M11 1h2v4h-2zM11 19h2v4h-2zM1 11h4v2H1zM19 11h4v2h-4z"/></svg>Services &amp; Pricing</div>
      <div class="menu-item"><svg viewBox="0 0 24 24" fill="#fff"><circle cx="7" cy="8" r="3"/><circle cx="17" cy="8" r="3"/><path d="M1 20c0-4 3-6 6-6s6 2 6 6zM11 20c0-4 3-6 6-6s6 2 6 6z"/></svg>Our Team</div>
      <div class="menu-item"><svg viewBox="0 0 24 24" fill="#fff"><circle cx="12" cy="7" r="4"/><path d="M4 22c0-5 4-8 8-8s8 3 8 8z"/></svg>Clients</div>
      <div class="menu-item"><svg viewBox="0 0 24 24" fill="#fff"><path d="M2 5h20v14H2z" opacity=".9"/><path d="m2 5 10 8 10-8" stroke="#4f86e3" stroke-width="2" fill="none"/></svg>Contact Us</div>
    </nav>
  </div>
  <div class="placeholder hero-art" role="img" aria-label="Cartoon illustration of a friendly dog working at a computer desk"></div>
  <h1 class="hero-title">The Design &amp; Marketing <em>Team That Always Puts</em> Honesty &amp; Care <em>Before</em> Profits</h1>
  <div class="hero-call">
    <span class="call-icon"><svg width="24" height="24" viewBox="0 0 24 24" fill="#fff"><path d="M6.6 10.8a15 15 0 0 0 6.6 6.6l2.2-2.2c.3-.3.7-.4 1-.2 1.1.4 2.3.6 3.6.6.6 0 1 .4 1 1V20c0 .6-.4 1-1 1A17 17 0 0 1 3 4c0-.6.4-1 1-1h3.5c.6 0 1 .4 1 1 0 1.3.2 2.5.6 3.6.1.3 0 .7-.2 1z"/></svg></span>
    Call Us Today
  </div>
  <div class="slide-arrow" style="left:0"><svg width="10" height="12" viewBox="0 0 10 12"><path d="M8 1 2 6l6 5" stroke="#fff" stroke-width="2" fill="none"/></svg></div>
  <div class="slide-arrow" style="right:0"><svg width="10" height="12" viewBox="0 0 10 12"><path d="m2 1 6 5-6 5" stroke="#fff" stroke-width="2" fill="none"/></svg></div>
</header>

<section class="about">
  <h2 class="section-title" style="top:52px">About <span>BrightHarbor.com</span></h2>
  <p class="section-lead" style="top:112px">We believe that honesty and steady effort come before personal profit. We are a family owned and operated company. Our parents raised us to take care of each other and that is exactly what we've done. We treat each of our clients with the same loyalty and respect that we give each other.</p>
  <p class="section-lead" style="top:160px">We are not looking to have hundreds and hundreds of clients. We are looking to expand our family with a handful of like-minded individuals. Companies who take pride in their work and their customers. We want to build mutually beneficial, lucrative, and long term partnerships.</p>
  <div class="about-actions">
    <span class="btn btn-orange"><svg width="14" height="14" viewBox="0 0 14 14"><path d="m4 2 6 5-6 5" stroke="#fff" stroke-width="2" fill="none"/></svg>Read More</span>
    <span class="btn btn-slate"><svg width="14" height="14" viewBox="0 0 24 24" fill="#fff"><path d="M6.6 10.8a15 15 0 0 0 6.6 6.6l2.2-2.2c.3-.3.7-.4 1-.2 1.1.4 2.3.6 3.6.6.6 0 1 .4 1 1V20c0 .6-.4 1-1 1A17 17 0 0 1 3 4c0-.6.4-1 1-1h3.5c.6 0 1 .4 1 1 0 1.3.2 2.5.6 3.6.1.3 0 .7-.2 1z"/></svg>Call Us Today</span>
  </div>
</section>

<section class="services">
  <h2 class="section-title" style="top:42px">Services We Provide</h2>
  <p class="section-lead" style="top:92px">Every service below is built around your goals, your budget and your customers, so your small business can grow with a team that cares about results as much as you do.</p>
  <svg class="abs" style="left:0;top:0" width="1200" height="758" viewBox="0 0 1200 758">
    <g transform="translate(0,-916)">
      <circle cx="600" cy="1320" r="205" fill="none" stroke="#6c7a96" stroke-width="2" stroke-dasharray="4 6"/>
      <circle cx="600" cy="1320" r="92" fill="#262b3d" stroke="#3f4866" stroke-width="3"/>
      <circle cx="600" cy="1320" r="52" fill="#ffffff"/>
      <g stroke="#6c7a96" stroke-width="2">
        <line x1="600" y1="1320" x2="520" y2="1130"/><line x1="600" y1="1320" x2="660" y2="1110"/>
        <line x1="600" y1="1320" x2="765" y2="1190"/><line x1="600" y1="1320" x2="770" y2="1370"/>
        <line x1="600" y1="1320" x2="730" y2="1465"/><line x1="600" y1="1320" x2="640" y2="1525"/>
        <line x1="600" y1="1320" x2="515" y2="1505"/><line x1="600" y1="1320" x2="435" y2="1400"/>
        <line x1="600" y1="1320" x2="420" y2="1220"/>
      </g>
      <g>
        <circle cx="520" cy="1130" r="36" fill="#f39c12"/><circle cx="660" cy="1110" r="36" fill="#29b6f6"/>
        <circle cx="765" cy="1190" r="36" fill="#8bc34a"/><circle cx="770" cy="1370" r="36" fill="#8e44ad"/>
        <circle cx="730" cy="1465" r="36" fill="#e74c3c"/><circle cx="640" cy="1525" r="36" fill="#1ab5c8"/>
        <circle cx="515" cy="1505" r="36" fill="#16a085"/><circle cx="435" cy="1400" r="36" fill="#f1c40f"/>
        <circle cx="420" cy="1220" r="36" fill="#e91e63"/>
      </g>
      <g fill="none" stroke="#fff" stroke-width="3">
        <circle cx="520" cy="1130" r="12"/>
        <rect x="646" y="1100" width="28" height="20"/>
        <path d="M753 1200l12-22 12 22z"/>
        <circle cx="770" cy="1364" r="7"/><path d="M756 1386c0-10 28-10 28 0"/>
        <path d="M718 1455h24v20h-24z"/>
        <circle cx="636" cy="1521" r="10"/><path d="m643 1528 9 9"/>
        <path d="M503 1505h24M515 1493v24"/>
        <rect x="423" y="1388" width="24" height="24"/>
        <path d="M408 1220h24M420 1208l12 12-12 12"/>
      </g>
      <g font-family="Open Sans,sans-serif" font-size="12" font-weight="700" fill="#fff" text-anchor="middle">
        <circle cx="545" cy="1165" r="12" fill="#2a86c9"/><text x="545" y="1169">1</text>
        <circle cx="690" cy="1145" r="12" fill="#2a86c9"/><text x="690" y="1149">2</text>
        <circle cx="735" cy="1225" r="12" fill="#2a86c9"/><text x="735" y="1229">3</text>
        <circle cx="730" cy="1385" r="12" fill="#2a86c9"/><text x="730" y="1389">4</text>
        <circle cx="700" cy="1440" r="12" fill="#2a86c9"/><text x="700" y="1444">5</text>
        <circle cx="640" cy="1480" r="12" fill="#2a86c9"/><text x="640" y="1484">6</text>
        <circle cx="540" cy="1470" r="12" fill="#2a86c9"/><text x="540" y="1474">7</text>
        <circle cx="470" cy="1380" r="12" fill="#2a86c9"/><text x="470" y="1384">8</text>
        <circle cx="455" cy="1230" r="12" fill="#2a86c9"/><text x="455" y="1234">9</text>
      </g>
    </g>
  </svg>
  <div class="service-label left" style="left:245px;top:148px"><h4>Consulting Service</h4><p>Clear advice on where to start and how to grow your business online.</p></div>
  <div class="service-label" style="left:712px;top:148px"><h4>Website Design &amp; Management</h4><p>Fast, friendly websites that we build, host and keep up to date.</p></div>
  <div class="service-label" style="left:820px;top:232px"><h4>Logo Design &amp; Branding Materials</h4><p>A look that customers remember on every card, sign and shirt.</p></div>
  <div class="service-label" style="left:826px;top:400px"><h4>Online Profile Design &amp; Management</h4><p>Every listing and profile kept accurate, polished and active.</p></div>
  <div class="service-label" style="left:785px;top:530px"><h4>Lead Gen Management</h4><p>Steady streams of new leads that turn into paying customers.</p></div>
  <div class="service-label" style="left:662px;top:630px"><h4>Search Engine Optimization</h4><p>Higher rankings so the right people find you first.</p></div>
  <div class="service-label left" style="left:242px;top:560px"><h4>Social Media Marketing</h4><p>Posts and campaigns that build a loyal local following.</p></div>
  <div class="service-label left" style="left:162px;top:420px"><h4>Marketing Material &amp; Print Design</h4><p>Flyers, brochures and mailers designed to get noticed.</p></div>
  <div class="service-label left" style="left:148px;top:278px"><h4>Outsourcing Management</h4><p>We coordinate trusted partners so nothing falls through.</p></div>
</section>

<section class="plans">
  <h2 class="section-title" style="top:46px">Select Your Plan</h2>
  <div class="floor" role="img" aria-label="Wooden floor boards"></div>

  <article class="plan-card" style="left:158px">
    <div class="plan-icon"><svg width="26" height="26" viewBox="0 0 24 24"><path d="M4 20 20 4M14 4h6v6" stroke="#2a86c9" stroke-width="2.5" fill="none"/></svg></div>
    <div class="plan-name">Basic Plan</div>
    <div class="plan-from">Starting from</div>
    <div class="plan-price"><sup>$</sup>52<small>.95</small></div>
    <ul class="plan-features"><li>Custom one page website</li><li>Basic logo design</li><li>Monthly site updates</li><li>Email support</li></ul>
    <div class="plan-foot"><span class="plan-btn primary">Get Started →</span><span class="plan-more">More Information ⓘ</span></div>
  </article>

  <article class="plan-card featured" style="left:395px">
    <div class="plan-icon"><svg width="26" height="26" viewBox="0 0 24 24"><path d="M3 12h18M12 3v18" stroke="#2a86c9" stroke-width="2.5"/></svg></div>
    <div class="plan-name">Standard Plan</div>
    <div class="plan-from">Starting from</div>
    <div class="plan-price"><sup>$</sup>114<small>.00</small></div>
    <ul class="plan-features"><li>Five page website</li><li>Logo and branding kit</li><li>Social media setup</li><li>Weekly site updates</li><li>Phone support</li></ul>
    <div class="plan-foot"><span class="plan-btn">Get Started →</span><span class="plan-more">More Information ⓘ</span></div>
  </article>

  <article class="plan-card" style="left:632px">
    <div class="plan-icon"><svg width="26" height="26" viewBox="0 0 24 24"><circle cx="10" cy="10" r="6" stroke="#f39c12" stroke-width="2.5" fill="none"/><path d="m15 15 6 6" stroke="#f39c12" stroke-width="2.5"/></svg></div>
    <div class="plan-name">Gold Plan</div>
    <div class="plan-from">Starting from</div>
    <div class="plan-price"><sup>$</sup>200<small>.95</small></div>
    <ul class="plan-features"><li>Ten page website</li><li>Search optimization</li><li>Social media posting</li><li>Print design credits</li></ul>
    <div class="plan-foot"><span class="plan-btn">Get Started →</span><span class="plan-more">More Information ⓘ</span></div>
  </article>

  <article class="plan-card" style="left:869px">
    <div class="plan-icon"><svg width="26" height="26" viewBox="0 0 24 24"><path d="m12 3 2.7 5.6 6.1.9-4.4 4.3 1 6.1L12 17l-5.4 2.9 1-6.1-4.4-4.3 6.1-.9z" fill="#f39c12"/></svg></div>
    <div class="plan-name">Platinum Plan</div>
    <div class="plan-from">Starting from</div>
    <div class="plan-price"><sup>$</sup>490<small>.00</small></div>
    <ul class="plan-features"><li>Unlimited page website</li><li>Full brand package</li><li>Lead gen campaigns</li><li>Dedicated manager</li></ul>
    <div class="plan-foot"><span class="plan-btn">Get Started →</span><span class="plan-more">More Information ⓘ</span></div>
  </article>
</section>

<section class="video">
  <div class="placeholder video-scene" role="img" aria-label="Photo of a laptop and coffee cup on a desk in front of a city skyline"></div>
  <div class="placeholder video-screen" role="img" aria-label="Laptop screen showing the company video"></div>
  <div class="play"><svg width="24" height="24" viewBox="0 0 24 24"><path d="M7 4v16l13-8z" fill="#333"/></svg></div>
  <h2 class="section-title">Watch Video</h2>
  <div class="video-band"><p>See how our family team helps small business owners grow with honest design, smart marketing and real care</p></div>
</section>

<section class="clients">
  <h2 class="section-title" style="top:56px">Our Clients</h2>
  <p class="section-lead" style="top:108px">Local shops, builders, clinics and service companies trust us with their brand. Here are a few of the partners we are proud to call part of our family.</p>
  <span class="row-arrow" style="left:110px">‹</span>
  <span class="row-arrow" style="left:1078px">›</span>
  <div class="client-row">
    <span class="client"><i></i>Marlowe</span>
    <span class="client"><i></i>Kestrel</span>
    <span class="client">Kestrel</span>
    <span class="client">Tidewell</span>
    <span class="client"><i></i>Marlowe</span>
    <span class="client"><i></i>Fernbrook</span>
    <span class="client">Alderpoint</span>
    <span class="client">Alderpoint</span>
  </div>
</section>

<section class="why">
  <h2 class="section-title" style="top:56px">Why Choose Us</h2>
  <p class="section-lead" style="top:108px">We keep our promises, we answer the phone, and we treat your business like our own. That is why our clients stay with us year after year.</p>
  <svg class="abs" style="left:0;top:0" width="1200" height="521" viewBox="0 0 1200 521">
    <path d="M380 222 Q600 120 820 222 M430 330 Q600 430 770 330" stroke="#9bb3cc" stroke-width="2" stroke-dasharray="3 6" fill="none"/>
    <circle cx="600" cy="270" r="86" fill="#ffffff"/>
    <circle cx="600" cy="270" r="62" fill="#1f6fc4"/>
  </svg>
  <div class="why-icon" style="left:434px;top:208px;background:#f47b20"><svg width="22" height="22" viewBox="0 0 24 24"><path d="m4 12 5 5 11-11" stroke="#fff" stroke-width="3" fill="none"/></svg></div>
  <div class="why-item" style="left:150px;top:206px;text-align:right"><h4>100% Risk Free Investment</h4><p>Try us without worry. If you are not happy, you do not pay.</p></div>
  <div class="why-icon" style="left:722px;top:208px;background:#1f6fc4"><svg width="22" height="22" viewBox="0 0 24 24"><rect x="3" y="6" width="18" height="12" stroke="#fff" stroke-width="2.5" fill="none"/><path d="M3 10h18" stroke="#fff" stroke-width="2.5"/></svg></div>
  <div class="why-item right" style="left:780px;top:206px"><h4>Multiple Payment Options Available</h4><p>Pay monthly, quarterly or yearly in the way that suits you.</p></div>
  <div class="why-icon" style="left:455px;top:318px;background:#1f6fc4"><svg width="22" height="22" viewBox="0 0 24 24"><path d="M12 21s-8-5-8-11a4 4 0 0 1 8-1 4 4 0 0 1 8 1c0 6-8 11-8 11z" fill="#fff"/></svg></div>
  <div class="why-item" style="left:170px;top:318px;text-align:right"><h4 style="color:#1f6fc4">Customer Loyalty Program</h4><p>Long term clients earn free extras and reduced rates.</p></div>
  <div class="why-icon" style="left:700px;top:318px;background:#1f6fc4"><svg width="22" height="22" viewBox="0 0 24 24"><circle cx="12" cy="8" r="4" fill="#fff"/><path d="M4 21c0-5 4-7 8-7s8 2 8 7z" fill="#fff"/></svg></div>
  <div class="why-item right" style="left:758px;top:318px"><h4>Unmatched Personal Service</h4><p>You always talk with a real person who knows your business.</p></div>
  <div class="why-icon" style="left:578px;top:376px;background:#f47b20"><svg width="22" height="22" viewBox="0 0 24 24"><circle cx="12" cy="12" r="8" stroke="#fff" stroke-width="2.5" fill="none"/><path d="M12 7v5l3 3" stroke="#fff" stroke-width="2.5" fill="none"/></svg></div>
  <div class="why-item" style="left:465px;top:428px;text-align:center"><h4 style="color:#1f6fc4">24/7 U.S. Based Customer Support</h4><p>Help is here any hour of the day, any day of the week.</p></div>
</section>

<section class="team">
  <h2 class="section-title" style="top:56px">Our Team</h2>
  <p class="section-lead" style="top:108px">Meet the people behind every project. We are a small family team who personally handle your design, marketing and support from day one.</p>
  <span class="row-arrow" style="left:110px;top:230px">‹</span>
  <span class="row-arrow" style="left:1078px;top:230px">›</span>
  <article class="team-card" style="left:145px">
    <div class="team-photo" role="img" aria-label="Portrait photo of the chief executive officer"></div>
    <div class="team-name">DANIEL PORTER</div>
    <div class="team-role">Chief Executive Officer</div>
    <p class="team-bio">Daniel leads our strategy and makes sure every client gets honest advice, fair pricing and work we are proud of ... [+]</p>
  </article>
  <article class="team-card" style="left:635px">
    <div class="team-photo" role="img" aria-label="Portrait photo of the chief operations officer"></div>
    <div class="team-name">OWEN HALE</div>
    <div class="team-role">Chief Operations Officer</div>
    <p class="team-bio">Owen keeps projects on time and on budget, and he is the first to pick up the phone when you need us ... [+]</p>
  </article>
</section>

<section class="inquiry">
  <h2 class="section-title" style="top:42px">Quick Inquiry</h2>
  <div class="placeholder inquiry-art" role="img" aria-label="Photo of hands typing on a laptop beside a coffee cup"></div>
  <div class="field" style="left:488px;top:102px;width:250px"><span>First Name</span><div></div></div>
  <div class="field" style="left:758px;top:102px;width:250px"><span>Last Name</span><div></div></div>
  <div class="field" style="left:488px;top:158px;width:250px"><span>Email</span><div></div></div>
  <div class="field" style="left:758px;top:158px;width:250px"><span>Phone Number</span><div></div></div>
  <div class="field area" style="left:488px;top:214px;width:520px"><span>Details About Your Enquiry</span><div></div></div>
  <div class="submit">SUBMIT</div>
</section>

<footer class="site-footer">
  <div class="foot-col" style="left:145px">
    <h5>Quick <span>Links</span></h5>
    <ul><li>Home</li><li>Services</li><li>Pricing</li><li>Our Team</li><li>Success Stories</li><li>Clients</li><li>Contact Us</li></ul>
  </div>
  <div class="foot-col" style="left:340px">
    <h5>Contact <span>Details</span></h5>
    <div style="line-height:18px">Bright Harbor LLC<br>Street Name, City, State<br>Post Code</div>
    <div class="contact-line" style="margin-top:8px"><b></b>555-010-4821</div>
    <div class="contact-line"><b></b>555-010-4822</div>
    <div class="contact-line"><b></b>hello@brightharbor.com</div>
  </div>
  <div class="foot-col" style="left:610px;width:260px">
    <h5>Newsletter <span>Signup</span></h5>
    <p style="line-height:18px">Get simple marketing tips and news from our team, once a month.</p>
    <div class="news-input">Email</div>
    <div class="news-btn">Subscribe</div>
  </div>
  <div class="copyright"><span>Copyright © 2017 BrightHarbor.com. All rights reserved</span><span>Terms of Use | Privacy Policy</span></div>
</footer>

</body>
</html>
```